Valderons Business Card

Business card for philanthropic organization

Industry/Entity Type

Business

Contact Information for Business Card

Need a very ELEGANT, sober, embossed, formal business card... it should transmit CREDIBILITY. Not looking for a "fun card". would like white, grays or black designs.

Font styles to use
Script

Requirements
Must have
• Embossed look

```html
<!DOCTYPE html>
<html lang="en">
<head>
<meta charset="utf-8">
<title>Valderons Business Card</title>
<link href="https://fonts.googleapis.com/css2?family=Lobster&family=Roboto:wght@400;500&display=swap" rel="stylesheet">
<style>
  :root {
    --page-bg: #d9d7d4;
    --card-bg: #1d1d1f;
    --card-edge: #2a2a2c;
    --text-main: #f2f2f2;
    --text-soft: #d8d8d8;
    --emboss-dark: #151516;
    --emboss-light: #3a3a3d;
    --emboss-shadow: #000000;
  }
  html, body {
    margin: 0;
    padding: 0;
    width: 1200px;
    height: 934px;
    overflow: hidden;
    background: var(--page-bg);
  }
  .canvas {
    position: relative;
    width: 1200px;
    height: 934px;
    display: flex;
    align-items: center;
    justify-content: center;
  }
  .business-card {
    position: relative;
    width: 1000px;
    height: 572px;
    background: var(--card-bg);
    border: 1px solid var(--card-edge);
    border-radius: 6px;
    box-shadow: 0 18px 40px rgba(0,0,0,0.25);
    font-family: "Roboto", Arial, sans-serif;
  }
  .brand-mark {
    position: absolute;
    left: 110px;
    top: 170px;
    width: 260px;
    display: flex;
    flex-direction: column;
    align-items: center;
    gap: 22px;
  }
  .brand-mark__circle {
    width: 120px;
    height: 120px;
    border-radius: 50%;
    background: var(--text-soft);
  }
  .brand-mark__name {
    font-family: "Roboto", Arial, sans-serif;
    font-weight: 400;
    font-size: 34px;
    color: var(--text-main);
    letter-spacing: 1px;
  }
  .identity {
    position: absolute;
    left: 470px;
    top: 150px;
    right: 60px;
  }
  .identity__name {
    font-family: "Lobster", cursive;
    font-size: 72px;
    line-height: 1;
    margin: 0 0 16px 0;
    color: var(--emboss-dark);
    text-shadow:
      -1px -1px 0 var(--emboss-light),
      2px 3px 3px var(--emboss-shadow);
  }
  .identity__role {
    font-size: 30px;
    line-height: 1.2;
    color: var(--text-main);
    margin: 0 0 30px 0;
  }
  .contact-list {
    list-style: none;
    margin: 0;
    padding: 0;
    font-size: 28px;
    line-height: 1.25;
    color: var(--text-main);
  }
  .contact-list__item {
    display: flex;
    align-items: flex-start;
    gap: 18px;
  }
  .contact-list__icon {
    flex: 0 0 22px;
    width: 22px;
    height: 22px;
    margin-top: 6px;
    fill: var(--text-main);
  }
  .contact-list__text { display: block; }
</style>
</head>
<body>
<main class="canvas">
  <section class="business-card" aria-label="Valderons business card">
    <div class="brand-mark">
      <div class="brand-mark__circle"></div>
      <div class="brand-mark__name">Valderons</div>
    </div>

    <div class="identity">
      <h1 class="identity__name">Marcelo Quintero</h1>
      <p class="identity__role">Abou Karim Valderons<br>Potentate 2017</p>

      <ul class="contact-list">
        <li class="contact-list__item">
          <svg class="contact-list__icon" viewBox="0 0 24 24" aria-hidden="true">
            <path d="M7 1h10a2 2 0 0 1 2 2v18a2 2 0 0 1-2 2H7a2 2 0 0 1-2-2V3a2 2 0 0 1 2-2zm0 3v14h10V4H7zm5 15.5a1.2 1.2 0 1 0 0 2.4 1.2 1.2 0 0 0 0-2.4z"/>
          </svg>
          <span class="contact-list__text">+(507)-6123-4480</span>
        </li>
        <li class="contact-list__item">
          <svg class="contact-list__icon" viewBox="0 0 24 24" aria-hidden="true">
            <path d="M2 5h20v14H2V5zm2 2v.4l8 5.2 8-5.2V7H4zm16 2.8-8 5.2-8-5.2V17h16V9.8z"/>
          </svg>
          <span class="contact-list__text">marcelo.quintero@mail.com</span>
        </li>
        <li class="contact-list__item">
          <svg class="contact-list__icon" viewBox="0 0 24 24" aria-hidden="true">
            <path d="M12 1a8 8 0 0 0-8 8c0 6 8 14 8 14s8-8 8-14a8 8 0 0 0-8-8zm0 11a3 3 0 1 1 0-6 3 3 0 0 1 0 6z"/>
          </svg>
          <span class="contact-list__text">P.O. Box 0816-02157<br>Panama, Republic of Panama</span>
        </li>
      </ul>
    </div>
  </section>
</main>
</body>
</html>
```